Kitchen and custom cabinetry company looking for business card design

We make: * Custom Kitchens, contemporary and traditional kitchens, Vanities, Libraries, Custom Entry Doors, Custom Wine Cellars and Custom Design Furniture. Phone number 555-284-7716. Address: Eastmere NY. Email: KAVRO@mailbox.example Portfolio at: KAVROcabinetry.example I would like moderns fonts and not heavy lines. double side but maybe will use clear plastic. I attached the logo.

Industry/Entity Type

Business

```html
<!DOCTYPE html>
<html lang="en">
<head>
<meta charset="utf-8">
<title>KAVRO Cabinetry Inc. – Business Card</title>
<link href="https://fonts.googleapis.com/css2?family=Cinzel:wght@400;700&family=Montserrat:wght@600&display=swap" rel="stylesheet">
<style>
  :root {
    --page-bg: #d8d3ce;
    --card-frost: #ebe8e5;
    --card-frost-light: #f4f2f0;
    --ink: #3f3f42;
    --ink-soft: #5b5b5f;
    --accent: #c8472b;
    --accent-dark: #a5341d;
    --band-grey: #5d5d60;
    --photo-cream: #d8cfc0;
    --photo-warm: #a98e6e;
    --photo-deep: #5a4a3a;
    --photo-stone: #8d8a86;
  }
  * { margin: 0; padding: 0; box-sizing: border-box; }
  html, body {
    width: 1200px; height: 970px; overflow: hidden;
    background: var(--page-bg);
  }
  .card {
    position: absolute; left: 75px; top: 193px;
    width: 1050px; height: 584px;
    background: linear-gradient(135deg, var(--card-frost-light), var(--card-frost));
    overflow: hidden;
    box-shadow: 0 10px 30px rgba(0,0,0,0.18);
    font-family: 'Cinzel', serif;
    color: var(--ink);
  }
  .card__photo {
    position: absolute; left: 388px; top: 0; right: 0; bottom: 0;
    background: linear-gradient(180deg, rgba(240,236,228,0.9) 0%, var(--photo-cream) 38%, var(--photo-stone) 60%, var(--photo-warm) 78%, var(--photo-deep) 100%);
    -webkit-mask-image: linear-gradient(90deg, transparent 0%, rgba(0,0,0,0.6) 25%, #000 45%);
    mask-image: linear-gradient(90deg, transparent 0%, rgba(0,0,0,0.6) 25%, #000 45%);
  }
  .brand { position: absolute; left: 46px; top: 50px; }
  .brand__name {
    font-family: 'Cinzel', serif; font-weight: 700;
    font-size: 50px; letter-spacing: 5px; line-height: 1;
    color: var(--ink);
  }
  .brand__name small { display: block; font-size: 22px; letter-spacing: 8.6px; margin-top: 4px; }
  .brand__tagline {
    margin-top: 7px;
    font-family: 'Montserrat', sans-serif; font-weight: 600;
    font-size: 12px; letter-spacing: 0.6px; color: var(--accent);
    text-transform: uppercase;
  }
  .person { position: absolute; left: 46px; top: 224px; }
  .person__name { font-size: 28px; font-weight: 700; color: var(--accent); line-height: 1.1; }
  .person__role { font-size: 21px; color: var(--ink-soft); margin-top: 4px; }
  .contacts { position: absolute; left: 46px; top: 332px; list-style: none; }
  .contacts li {
    display: flex; align-items: center; gap: 24px;
    height: 29px; font-size: 21px; color: var(--ink);
  }
  .contacts svg { width: 22px; height: 22px; fill: var(--accent); flex: none; }
  .location { position: absolute; left: 46px; top: 466px; font-size: 22px; color: var(--ink); }
  .band { position: absolute; left: 0; bottom: 0; width: 100%; height: 57px; }
</style>
</head>
<body>
  <div class="card">
    <div class="card__photo" role="img" aria-label="Photograph of a finished custom kitchen with cream cabinets, pendant lights and a stone island"></div>

    <div class="brand">
      <div class="brand__name">KAVRO<small>CABINETRY INC.</small></div>
      <div class="brand__tagline">Crafted Kitchens and Fine Interiors</div>
    </div>

    <div class="person">
      <div class="person__name">Dana Morrow</div>
      <div class="person__role">Manager</div>
    </div>

    <ul class="contacts">
      <li>
        <svg viewBox="0 0 24 24" aria-hidden="true"><path d="M3 9c0-3 4-5 9-5s9 2 9 5v2h-5V9c-2-.8-6-.8-8 0v2H3zM6 12h12l2 8H4z"/></svg>
        555-284-7716
      </li>
      <li>
        <svg viewBox="0 0 24 24" aria-hidden="true"><path d="M2 5h20v14H2zM4 7v.5l8 6 8-6V7zm0 3v7h16v-7l-8 6z"/></svg>
        KAVRO@MAILBOX.EXAMPLE
      </li>
      <li>
        <svg viewBox="0 0 24 24" aria-hidden="true"><path d="M2 3h20v14H14v2h3v2H7v-2h3v-2H2zm2 2v10h16V5z"/></svg>
        WWW.KAVROCABINETRY.EXAMPLE
      </li>
    </ul>

    <div class="location">Eastmere NY</div>

    <svg class="band" viewBox="0 0 1050 57" preserveAspectRatio="none" aria-hidden="true">
      <rect x="0" y="26" width="745" height="31" fill="var(--band-grey)"/>
      <polygon points="770,0 1050,0 1050,57 735,57" fill="var(--accent)"/>
      <polygon points="770,0 1050,0 1050,14 765,14" fill="var(--accent-dark)" opacity="0.35"/>
    </svg>
  </div>
</body>
</html>
```